Help Give House Painter “Fresh” Website Makeover!

A residential and commercial painting company based in Albuquerque, NM, USA needs a fresh, new, fun, and playful--yet, simple, elegant and professional--website made.

Here is a link to their existing site:

http://corvelcoatings.example/

We want to keep a similar site structure., So the navigation layout will stay the same. However, the video is too small, is too far over in the sidebar, and the overall design is amateur at best. We want something bright, colorful and bold!

We will need a space for the Video above the fold, and there needs to be space in the design for Testimonials, Specials and Images. It’s also very important to have the Pellham Roster awards that you see on his current website.

Please also include somewhere in the Design icons for YouTube, Facebook, Google+ and LinkedIn.

Here are some examples to look at to get your creative juices flowing!

http://brightloombrush.example/

http://www.tkvr.example/

http://www.marblow-tennick.example/

http://www.quarrypages.example/painting-company-niche-website/

http://www.brisklayoutdepot.example/website-templates/painting-company-website-template-53817.html

We have accounts at both lumavault.example and pixaroo.example. If you use placeholder images from there, that's fine. We can buy the images when and if your design is selected.

Target Market(s)

The audience is the average middle class homeowner to higher upper class. This should appeal to families, couples, and singles who own a home.

Industry/Entity Type

Residential

Font styles to use
Sans Serif

Requirements
Must have
• - - Lots of color! It's a site about painting homes. People like a variety of colors. Bring out your inner artist, and get bold with your colors!

- - A video place holder. As you can see, there is a video on the existing site, but it's small and hidden. Make it big and put it top left, or in the center.

- -Detailed and organized PSD structure. We're going to turn your design into a website, and to make that work soothly, we ask that you organize you PSD well: name your layers, keep things separated, group and ungroup as necessary, etc.

- A sidebar that goes down the right side of an interior page. We need a homepage, and also one [1] interior page template. We don't need you to make a design for each page. Just the homepage, followed by a simple interior page design that requires only the header/navigation, and a sidebar down the right side.
Should not have
• - Coding. This is a design project only.

```html
<!DOCTYPE html>
<html lang="en">
<head>
<meta charset="utf-8">
<title>Corvel Coatings – Home</title>
<link href="https://fonts.googleapis.com/css2?family=Lato:ital,wght@0,400;0,700;0,900;1,400;1,700&family=Roboto+Condensed:wght@400;700&display=swap" rel="stylesheet">
<style>
:root{
  --blue:#1a4aa0;
  --blue-dark:#0d4fa0;
  --nav-top:#2a98dc;
  --nav-bottom:#0a5fae;
  --red:#e31e2a;
  --form-red:#c8262e;
  --gold:#f0a81e;
  --yellow:#f6b52c;
  --text:#333;
  --muted:#666;
  --page:#f4f4f4;
  --white:#fff;
}
*{margin:0;padding:0;box-sizing:border-box}
html,body{width:789px;height:1200px;overflow:hidden}
body{position:relative;background:var(--white);font-family:'Lato',sans-serif;color:var(--text)}
.abs{position:absolute}
.cond{font-family:'Roboto Condensed',sans-serif}

/* header */
.site-header{left:0;top:0;width:789px;height:80px;background:var(--white)}
.brand-mark{left:88px;top:28px;width:26px;height:26px;border-radius:50%;background:var(--blue)}
.brand-name{left:124px;top:29px;font-size:21px;font-weight:700;color:var(--blue);letter-spacing:.3px}
.award{width:90px;text-align:center;font-size:8px;font-weight:700;color:#222}
.award-badge{display:block;margin:0 auto 6px;width:34px;height:44px;border-radius:5px;background:#d6a52a}
.phone{left:589px;top:34px;display:flex;align-items:center;gap:6px;font-size:16px;color:var(--red)}

/* nav */
.main-nav{left:0;top:80px;width:789px;height:30px;background:linear-gradient(var(--nav-top),var(--nav-bottom))}
.main-nav a{position:absolute;top:10px;font-size:9.4px;font-weight:700;color:var(--white);text-decoration:none;text-transform:uppercase;white-space:nowrap}
.main-nav a.active::after{content:"";position:absolute;left:0;right:0;top:16px;height:2px;background:var(--white)}

/* hero */
.hero{left:0;top:110px;width:789px;height:312px;background:repeating-linear-gradient(45deg,#353535 0 2px,#404040 2px 4px)}
.video{left:86px;top:110px;width:420px;height:238px;background:linear-gradient(90deg,#c85a12 0%,#e07a2a 45%,#d8d8d8 55%,#f2f2f2 100%)}
.video-title{left:86px;top:141px;width:214px;text-align:center;color:var(--white)}
.video-title .name{font-family:'Lato',sans-serif;font-size:13px;font-weight:900;color:var(--white);margin-bottom:5px}
.video-title .line{font-size:16px;line-height:19px}
.play{left:279px;top:211px;width:34px;height:22px;border-radius:5px;background:var(--red)}
.controls{left:86px;top:330px;width:420px;height:18px;background:linear-gradient(#3a3f4a,#1c1f26)}
.cta-band{left:86px;top:348px;width:420px;height:74px;background:var(--blue);color:var(--white);text-align:center}
.cta-band p{font-family:'Roboto Condensed',sans-serif;white-space:nowrap}
.cta-band .num{color:var(--yellow)}

/* estimate form */
.estimate{left:506px;top:110px;width:197px;height:312px;background:var(--form-red);color:var(--white)}
.estimate-head{height:30px;background:var(--gold);font-size:13.5px;font-weight:700;text-align:center;line-height:32px;letter-spacing:.3px}
.estimate h3{margin-top:27px;font-size:12.5px;text-align:center}
.estimate .intro{margin:4px 12px 0;font-size:8px;line-height:10.5px;text-align:center}
.field{position:absolute;left:11px;width:179px;background:var(--white);border-radius:3px;font-size:8px;color:#444;padding:4px 5px}
.captcha-label{position:absolute;left:11px;top:238px;font-size:8px}
.submit{position:absolute;left:11px;top:274px;width:86px;height:22px;border-radius:4px;background:linear-gradient(#f7bb3a,#e79612);font-size:11px;font-weight:700;text-align:center;line-height:22px}

/* main */
.page{left:0;top:422px;width:789px;height:590px;background:var(--page)}
.sidebar{left:506px;top:422px;width:197px;height:590px;background:var(--white)}
.section-title{font-size:12.5px;font-weight:700;color:var(--text);text-transform:uppercase;white-space:nowrap}
.section-title .hl{color:var(--red)}
.rule{height:2px;background:#ccc}
.rule::before{content:"";display:block;width:110px;height:2px;background:#555}
.intro-copy{left:86px;top:476px;width:410px;font-size:9.4px;line-height:13.6px;color:var(--text)}
.intro-copy p+p{margin-top:8px}
.btn-red{left:86px;top:618px;width:63px;height:22px;background:var(--red);border-radius:3px;color:var(--white);font-size:9px;font-weight:700;text-align:center;line-height:22px}

.service{width:130px;height:120px;border-radius:6px;overflow:hidden;color:var(--white);text-align:center}
.service .title{height:63px;padding-top:46px;font-size:9.5px;font-weight:700;white-space:nowrap}
.service .blurb{height:35px;background:var(--yellow);color:#333;font-size:7.6px;font-weight:700;padding:6px 8px 0;line-height:10.5px}
.service .more{height:22px;font-size:8.5px;font-weight:700;text-decoration:underline;line-height:22px}
.thumb{width:76px;height:76px;border-radius:50%;border:3px solid var(--white)}

.quote{left:517px;width:174px;height:106px;background:#e6e6e6;border-radius:6px 6px 6px 24px;padding:8px 8px 0 29px;font-size:7.6px;font-style:italic;line-height:12.5px;color:#333}
.quote::before{content:"“";position:absolute;left:10px;top:0;font-size:28px;color:#bbb;font-style:normal}
.avatar{width:50px;height:50px;border-radius:50%;background:linear-gradient(#5a6a7c,#1e2a38);border:2px solid var(--white);box-shadow:0 0 0 1px #ccc}
.author{font-size:8px;font-weight:700;color:var(--blue)}
.promo{left:517px;width:174px;height:84px}
.promo-specials{top:801px;background:linear-gradient(90deg,#d81e22 0%,#d81e22 50%,#fff 60%);border-right:6px solid #111;border-top:1px solid #111;border-bottom:1px solid #111}
.promo-specials span{position:absolute;right:16px;top:22px;font-size:14px;font-style:italic;font-weight:700;color:var(--red);text-decoration:underline;line-height:18px;text-align:right}
.promo-check{top:910px;background:linear-gradient(160deg,#e4c79a 0%,#a8713a 55%,#6e3e18 100%)}
.promo-check span{position:absolute;right:12px;bottom:12px;font-size:15px;font-style:italic;font-weight:700;color:var(--white);text-decoration:underline}

/* footer */
.site-footer{left:0;top:1012px;width:789px;height:188px;background:var(--blue-dark);color:var(--white)}
.quick{left:86px;top:1012px;width:167px;height:188px;background:var(--white)}
.quick-head{height:28px;background:linear-gradient(var(--gold),#e89612);font-size:11.5px;color:var(--white);line-height:28px;padding-left:14px}
.quick ul{list-style:none;margin-top:10px}
.quick li{font-size:8.5px;font-weight:700;color:#222;height:16.5px;padding-left:34px;position:relative;line-height:11px}
.quick li::before{content:"";position:absolute;left:15px;top:2px;width:7px;height:7px;border-radius:50%;background:var(--blue)}
.foot-title{font-size:12px;font-weight:700}
.email-input{left:277px;top:1049px;width:207px;height:24px;background:var(--white);font-size:7.5px;color:#999;padding:8px 8px}
.email-btn{left:488px;top:1049px;width:55px;height:24px;background:var(--red);font-size:10px;font-weight:700;text-align:center;line-height:24px}
.divider-v{width:1px;background:#3a6fb8}
.contact{font-size:8.5px;line-height:14px}
.badge-box{left:591px;top:1102px;width:113px;height:45px;background:var(--white);border-radius:4px}
.copy{left:253px;top:1174px;width:450px;text-align:center;font-size:8.5px;font-weight:700}
</style>
</head>
<body>

<header class="site-header abs">
  <div class="brand-mark abs"></div>
  <div class="brand-name abs">CORVEL COATINGS</div>
  <div class="award abs" style="left:380px;top:9px">
    <span class="award-badge" role="img" aria-label="Pellham Roster award badge"></span>
    EXTERIOR PAINTING
  </div>
  <div class="award abs" style="left:470px;top:9px">
    <span class="award-badge" role="img" aria-label="Pellham Roster award badge"></span>
    INTERIOR PAINTING
  </div>
  <div class="phone abs">
    <svg width="17" height="17" viewBox="0 0 24 24"><circle cx="12" cy="12" r="10.5" fill="none" stroke="#1a4aa0" stroke-width="2"/><path d="M8.5 7c.5-.6 1.3-.5 1.6.1l.8 1.6c.2.5 0 1-.4 1.3l-.6.4c.6 1.4 1.7 2.5 3.1 3.1l.4-.6c.3-.4.8-.6 1.3-.4l1.6.8c.6.3.7 1.1.1 1.6-1 1-2.4 1.2-3.6.6-2.3-1.2-4-2.9-5.2-5.2-.6-1.2-.4-2.6.9-3.3z" fill="#1a4aa0"/></svg>
    123 456 7890
  </div>
</header>

<nav class="main-nav abs">
  <a class="active" style="left:85px">Home</a>
  <a style="left:126px">About Us</a>
  <a style="left:187px">Residential Painting</a>
  <a style="left:307px">Commercial Painting</a>
  <a style="left:432px">FAQ</a>
  <a style="left:466px">Specials</a>
  <a style="left:522px">Blog</a>
  <a style="left:562px">Testimonials</a>
  <a style="left:644px">Contact Us</a>
</nav>

<section class="hero abs"></section>
<div class="video abs" role="img" aria-label="Video still: bedroom half painted orange, half white"></div>
<div class="video-title abs cond">
  <div class="name">CORVEL COATINGS</div>
  <div class="line">RESIDENTIAL &amp; COMMERCIAL</div>
  <div class="line">PAINTING COMPANY</div>
</div>
<div class="play abs"><svg width="34" height="22"><path d="M14 6l8 5-8 5z" fill="#fff"/></svg></div>
<div class="controls abs">
  <svg width="420" height="18">
    <rect x="6" y="4" width="14" height="10" rx="2" fill="#5a6a88"/><path d="M11 6.5l4 2.5-4 2.5z" fill="#fff"/>
    <rect x="32" y="7" width="126" height="4" rx="2" fill="#bbb"/><circle cx="62" cy="9" r="3" fill="#eee"/>
    <text x="164" y="12" font-size="6" fill="#ddd" font-family="Lato,sans-serif">1:47  /  12:35</text>
    <rect x="360" y="4" width="14" height="10" rx="2" fill="#5a6a88"/><rect x="379" y="4" width="14" height="10" rx="2" fill="#5a6a88"/><rect x="398" y="4" width="14" height="10" rx="2" fill="#5a6a88"/>
  </svg>
</div>
<div class="cta-band abs">
  <p style="font-size:13px;margin-top:9px">Need Painting In The Albuquerque Area?</p>
  <p style="font-size:16px;margin-top:4px">Call Dale Today For Your FREE Painting Estimate! <span class="num">555-0148</span></p>
  <p style="font-size:13.5px;margin-top:4px">Licensed - Bonded - Insured</p>
</div>

<aside class="estimate abs">
  <div class="estimate-head">SCHEDULE FREE ESTIMATE</div>
  <h3>How to Schedule an Estimae</h3>
  <p class="intro">Requesting an estimate online is very simple and easy. Fill out the Form below and we will send you a rough quote to your email. We may also call you if we have any more questions.</p>
  <div class="field" style="top:128px;height:16px;padding-top:3px">Name:</div>
  <div class="field" style="top:151px;height:16px;padding-top:3px">Email:</div>
  <div class="field" style="top:173px;height:16px;padding-top:3px">Phone:</div>
  <div class="field" style="top:195px;height:37px">Decribe what needs to be done.</div>
  <div class="captcha-label">Please type the following</div>
  <div class="field" style="top:250px;height:17px;padding-top:3px">ac2gH</div>
  <div class="submit">Submit Now</div>
</aside>

<main class="page abs"></main>
<div class="sidebar abs"></div>

<h2 class="section-title abs" style="left:87px;top:446px">Welcome to <span class="hl">Corvel Coatings</span></h2>
<div class="rule abs" style="left:86px;top:462px;width:408px"></div>
<div class="intro-copy abs">
  <p>Corvel Coatings does jobs as small as a bathroom up to large commercial projects right here in Albuquerque and Rio Rancho. Extensive as an entire apartment exterior, to a kitchen and all home interior, no job is too big or too small for Corvel Coatings of Albuquerque. Corvel Coatings is staffed with the best painters for the highest quality paint jobs. Corvel Coatings is not a community’s average house painter staffing company, but this painting company is staffed with professional painters that pride themselves on successfully completing every job.</p>
  <p>Dale Hirsch, owner of Corvel Coatings, Inc., started painting in 1975 during high school. He continued painting through college where he earned a Bachelor of Science degree from Pralton University in 1984. Dale opened his first painting company in 1984.</p>
</div>
<div class="btn-red abs">Read More</div>

<div class="service abs" style="left:86px;top:697px;background:#f26a0a"><div class="title">COMMERCIAL PAINTING</div><div class="blurb">Lorem ipsum dolor sit a consecte adipiscing Lorem ipsum...</div><div class="more" style="background:#e05a00">Read more</div></div>
<div class="service abs" style="left:224px;top:697px;background:#2382b8"><div class="title">RESIDENTIAL PAINTING</div><div class="blurb">Lorem ipsum dolor sit a consecte adipiscing Lorem ipsum...</div><div class="more" style="background:#1a6fa2">Read more</div></div>
<div class="service abs" style="left:363px;top:697px;background:#3a9a0a"><div class="title">STUCCO COATINGS</div><div class="blurb">Lorem ipsum dolor sit a consecte adipiscing Lorem ipsum...</div><div class="more" style="background:#2e8806">Read more</div></div>
<div class="service abs" style="left:86px;top:873px;background:#12337f"><div class="title">CABINETS</div><div class="blurb">Lorem ipsum dolor sit a consecte adipiscing Lorem ipsum...</div><div class="more" style="background:#0d2a6c">Read more</div></div>
<div class="service abs" style="left:224px;top:873px;background:#e31e2a"><div class="title">INTERIOR/ EXTERIOR</div><div class="blurb">Lorem ipsum dolor sit a consecte adipiscing Lorem ipsum...</div><div class="more" style="background:#cc1520">Read more</div></div>
<div class="service abs" style="left:363px;top:873px;background:#c88408"><div class="title" style="font-size:9px">DRY WALL TEXTURE REPAIR</div><div class="blurb">Lorem ipsum dolor sit a consecte adipiscing Lorem ipsum...</div><div class="more" style="background:#b07204">Read more</div></div>

<div class="thumb abs" style="left:113px;top:659px;background:radial-gradient(#f2d060,#c49a20)" role="img" aria-label="Roller applying yellow paint"></div>
<div class="thumb abs" style="left:251px;top:659px;background:radial-gradient(#e8eef2,#9ab4c4)" role="img" aria-label="Painter at work indoors"></div>
<div class="thumb abs" style="left:390px;top:659px;background:radial-gradient(#9a6a50,#5a2e34)" role="img" aria-label="Textured stucco wall"></div>
<div class="thumb abs" style="left:113px;top:835px;background:radial-gradient(#f4f4f4,#a8a8a8)" role="img" aria-label="White kitchen cabinets"></div>
<div class="thumb abs" style="left:251px;top:835px;background:radial-gradient(#e8a04a,#3a3046)" role="img" aria-label="House exterior lit at dusk"></div>
<div class="thumb abs" style="left:390px;top:835px;background:radial-gradient(#4a8ad8,#1a4a9a)" role="img" aria-label="Blue paint on roller"></div>

<h2 class="section-title abs" style="left:518px;top:446px;color:var(--blue)">Client <span class="hl">Testimonials</span></h2>
<div class="rule abs" style="left:517px;top:462px;width:174px"></div>

<div class="quote abs" style="top:478px">Lorem ipsum dolor sit amet, consecte adipiscing elit, sed diam nonum euismod tincidunt ut laoreet dolore magna aliquam erat volutpat. Ut wisi enim ad mi veniam, quis nostrud exerci tation ullamco suscipit lobortis nisl ut aliquip ex .</div>
<div class="avatar abs" style="left:533px;top:570px" role="img" aria-label="Client portrait"></div>
<div class="author abs" style="left:595px;top:597px">Mr. Dolore Magna</div>

<div class="quote abs" style="top:636px">Lorem ipsum dolor sit amet, consecte adipiscing elit, sed diam nonum euismod tincidunt ut laoreet dolore magna aliquam erat volutpat. Ut wisi enim ad mi veniam, quis nostrud exerci tation ullamco suscipit lobortis nisl ut aliquip ex .</div>
<div class="avatar abs" style="left:533px;top:727px" role="img" aria-label="Client portrait"></div>
<div class="author abs" style="left:595px;top:754px">Mr. Dolore Magna</div>

<div class="promo promo-specials abs" role="img" aria-label="Paint roller on red wall"><span>Our<br>Specials!</span></div>
<div class="promo promo-check abs" role="img" aria-label="Paint roller on wooden floor"><span>Check Out</span></div>

<footer class="site-footer abs"></footer>
<div class="quick abs">
  <div class="quick-head">Quick Links</div>
  <ul>
    <li>HOME</li><li>ABOUT US</li><li>RESIDENTIAL PAINTING</li><li>COMMERCIAL PAINTING</li><li>FAQ</li><li>SPECIALS</li><li>BLOG</li><li>TESTIMONIALS</li><li>CONTACT US</li>
  </ul>
</div>

<div class="foot-title abs" style="left:279px;top:1027px;color:#fff">Sign up for Newsletter</div>
<div class="email-input abs">Enter Your Email</div>
<div class="email-btn abs" style="color:#fff">SUBMIT</div>

<div class="divider-v abs" style="left:567px;top:1030px;height:48px"></div>
<div class="foot-title abs" style="left:592px;top:1027px;color:#fff">Follow Us On</div>
<svg class="abs" style="left:589px;top:1049px" width="106" height="24" viewBox="0 0 106 24">
  <path d="M11 1l10 5.5v11L11 23 1 17.5v-11z" fill="#2a5f98"/>
  <path d="M38 1l10 5.5v11L38 23l-10-5.5v-11z" fill="#2e8ac8"/>
  <path d="M65 1l10 5.5v11L65 23l-10-5.5v-11z" fill="#1f5c8e"/>
  <path d="M92 1l10 5.5v11L92 23l-10-5.5v-11z" fill="#c23a2a"/>
</svg>

<div class="abs" style="left:277px;top:1090px;width:426px;height:1px;background:#3a6fb8"></div>

<svg class="abs" style="left:277px;top:1105px" width="11" height="15" viewBox="0 0 12 16"><path d="M6 0a6 6 0 016 6c0 4.5-6 10-6 10S0 10.5 0 6a6 6 0 016-6z" fill="#fff"/><circle cx="6" cy="6" r="2.3" fill="#0d4fa0"/></svg>
<div class="contact abs" style="left:296px;top:1105px;color:#fff">Corvel Coatings Inc.<br>4120 Tamsen Road Northeast,<br>Albuquerque, NM 87109</div>

<svg class="abs" style="left:463px;top:1106px" width="12" height="12" viewBox="0 0 24 24"><path d="M5 2c1-.9 2.4-.8 3 .3l2 3.6c.4.8.2 1.7-.5 2.3l-1.3 1c1.2 2.6 3.1 4.5 5.7 5.7l1-1.3c.6-.7 1.5-.9 2.3-.5l3.6 2c1.1.6 1.2 2 .3 3-2 2-5 2.4-7.5 1-4.3-2.4-7.4-5.5-9.8-9.8C1.4 6.8 2.4 4 5 2z" fill="#fff"/></svg>
<div class="contact abs" style="left:481px;top:1105px;color:#fff">555-0193</div>
<svg class="abs" style="left:428px;top:1131px" width="13" height="10" viewBox="0 0 13 10"><rect x=".5" y=".5" width="12" height="9" fill="#fff"/><path d="M.5 .5l6 5 6-5" fill="none" stroke="#0d4fa0" stroke-width="1"/></svg>
<div class="contact abs" style="left:447px;top:1129px;color:#fff">info@corvelcoatings.example</div>

<div class="divider-v abs" style="left:567px;top:1100px;height:50px"></div>
<div class="badge-box abs">
  <svg width="113" height="45" role="img" aria-label="Accreditation badge"><rect x="16" y="8" width="80" height="29" rx="3" fill="#1a5a8a"/></svg>
</div>

<div class="abs" style="left:277px;top:1160px;width:426px;height:1px;background:#3a6fb8"></div>
<div class="copy abs" style="color:#fff">© 2015 CORVEL COATINGS. All Rights Reserved.</div>

</body>
</html>
```